QUORVIN CAPABILITY STATEMENT “Shaping Lasting Links”

QUORVIN CAPABILITY STATEMENT
“Shaping Lasting Links”
Indigenous-Owned Telecommunications & Infrastructure Solutions Partner

COVER PAGE

Visual: Modern and clean design featuring telecom towers, wind turbines, civil infrastructure, roads, and community WiFi imagery.
Tagline: “Linking Places, Lifting Futures.”
Contact:
Website: www.quorvin.com.au
Email: info@quorvin.com.au
Phone: [Insert Main Number]
“Proudly Indigenous-Owned | Compliant with Aboriginal Procurement Policy (APP) & SME Policies”
INTRODUCTION

Quorvin is a 100% Indigenous-owned leader in comprehensive infrastructure solutions, specializing in telecommunications, civil works, renewable energy, structural engineering, and site development. With over a decade of experience, we deliver safe, reliable, and culturally respectful services across Australia, from urban centers to remote wind farms and heritage sites. Our mission: “To bridge infrastructure gaps while empowering Indigenous communities and fostering sustainable growth.”

CORE CAPABILITIES

TELECOMMUNICATIONS

Tower Builds & Maintenance: Structural engineering, geotechnical analysis, foundation mapping.
Community WiFi Projects: Enhancing digital inclusion in Indigenous and remote communities.
Fiber & Wireless Networks: End-to-end installation for Velonet, Satellite, and regional connectivity.
Height Safety Systems: Design, inspection, and certification of lad-safe safety infrastructure.
CIVIL & STRUCTURAL ENGINEERING

Foundations & Concreting: Reinforced slabs, grillage, geotech-to-construction turnkey solutions.
Site Development: Earthworks, drainage, and access road/track construction.
Wind Farm Infrastructure: Reinforcing towers and integrating power systems for high-wind environments.
ROAD & ACCESS TRACK CONSTRUCTION

Construction of durable access roads and tracks: For remote projects and urban settings.
Remediation of existing tracks: Upgrading for environmental compliance and sustainability.
Facilitating logistics and site access: Particularly in challenging terrain.
POWER & ELECTRICAL SYSTEMS

Off-grid energy solutions: Solar hybrid systems, electrical structural engineering.
Grid upgrades: Ensuring compliance with AS/NZS standards and facilitating connection upgrades.
SITE REFURBISHMENT & DEMOLITION

Comprehensive refurbishment and demolition services: For outdated telecom sites and structures.
Environmentally responsible dismantling: Focused on recycling materials and minimizing land impact.
EMERGENCY RESPONSE SERVICES

24/7 Rapid Response: Over 450 callouts annually; 4,000+ emergencies resolved nationwide.
Disaster Recovery: Comprehensive support during floods, bushfires for Velonet, Marvaske, Trilumen, and regional clients.
PROJECT EXPERIENCE

Heritage Tower Upgrade

Enhanced safety and technology on culturally significant heritage sites, preserving their integrity.
Wind Farm Deployment

Delivered power, fiber, and reinforced foundations for large-scale renewable energy projects in high-wind environments.
Regional Fibre Network

Laid 200km of fiber in flood-prone regions, ensuring critical infrastructure resilience.
Indigenous Community WiFi & Connectivity

Installed sustainable WiFi networks to bridge the digital divide, supporting education, health, and business activities.
Site Demolition & Refurbishment

Safely decommissioned aging telecom sites and structures across Australia, emphasizing land reuse and environmental care.
Access Track Construction & Remediation

Developed new access roads and refurbished existing tracks to facilitate project logistics, particularly in remote or environmentally sensitive areas.
Key Stats:
+600 sites supported | 10-year Velonet partner | 98% client retention | Over 20 Indigenous community WiFi deployments

COMMITMENT TO SAFETY & QUALITY

“Pause Twice, Work Wise” Protocol: Enforced pre-task risk assessments to ensure safety at every stage.
Certifications: ISO 45001 (Safety) | ISO 9001 (Quality Management).
Safety Culture: Regular safety audits, Indigenous-led training programs, and safety initiatives focused on community well-being.
INDIGENOUS INCLUSION & COMMUNITY IMPACT

Elders Guidance Council: Provides guidance on community engagement, cultural sensitivity, and social responsibility.
Supplier Diversity: 30% procurement from Indigenous-owned businesses, fostering economic growth.
Regional Employment: 65% of our workforce originates from local communities, creating sustainable jobs.
Testimonial: “Quorvin’s partnership empowered our community with jobs and infrastructure that respects our land.” – Local Indigenous Leader

CONTACT & SERVICE AREAS

Headquarters: [Insert Address] | ABN: [Insert ABN]

24/7 Emergency Support: [Insert Dedicated Emergency Line]

Certifications & Registrations:

Trade Circle Registered, First Enterprise Register (FER)
SERVICE AREAS

National Coverage with Regional Expertise:
Major Cities: Sydney, Melbourne, Brisbane, Perth, Adelaide, Darwin, Hobart.
Regional & Remote Areas: Pilbara, Kimberley, Far North Queensland, Outback NSW.
Disaster Zones: Rapid response teams deployed nationwide for bushfire and flood incidents.
EMERGENCY SUPPORT

SLA Guarantee: 90% of emergencies addressed within 4 hours.
Partners Supported: Velonet, Marvaske, Trilumen, regional councils.
This capability statement reflects our commitment to quality, safety, and community engagement across all levels of operation, ensuring that we empower the communities we serve while maintaining the highest standards of service delivery.

Target Market(s)

Government Agencies: Especially those seeking to comply with Indigenous Procurement Policies. Telecommunication Operators: Such as Velonet, Marvaske, and Trilumen for infrastructure deployment. Indigenous Communities: Projects aimed at enhancing connectivity and digital inclusion. Utilities and Energy Providers: For power and electrical infrastructure projects. Construction and Engineering Firms: Seeking collaboration on civil and structural infrastructure projects.

Industry/Entity Type

Telecommunications and Infrastructure Development: Focused on service delivery in various contexts, including urban settings, remote locations, and Indigenous community projects. Renewable Energy: This includes wind and solar infrastructure linked to telecommunications enhancements. Civil Engineering: Related to building and maintaining essential infrastructure such as access roads and utility lines.

Font styles to use
Other font styles liked:
• Bubbleboddy neue

Requirements
Must have
• Clear demonstration of Indigenous ownership and community engagement. Compliance with relevant safety and quality certifications (e.g., ISO 45001, ISO 9001). Showcase of core capabilities in telecommunications, civil engineering, and those specific to renewable energy. Visuals that reflect the diverse range of services offered (like telecom towers and community WiFi installations).
Nice to have
• Interactive elements such as hyperlinks to project case studies or client testimonials. Infographics or visual data to highlight key statistics and project success rates. Cultural motifs or imagery that reflect Indigenous heritage and inclusion in design aspirations. QR codes that link to videos or more detailed project descriptions for digital formats.
Should not have
• Clutter or excessive text that detracts from the main messages. Generic stock images that don’t align with the specific projects or Indigenous culture. Technical jargon that could confuse stakeholders unfamiliar with industry-specific terms. Overemphasis on competitors; the focus should remain on Quorvin's unique strengths and contributions.

```html
<!DOCTYPE html>
<html lang="en">
<head>
<meta charset="utf-8">
<title>Quorvin Capability Statement – Services & Commitments</title>
<link rel="stylesheet" href="https://fonts.googleapis.com/css2?family=Barlow:wght@400;600;700&family=Righteous&display=swap">
<style>
  :root {
    --brand-red: #e5322d;
    --ink: #1c1c1c;
    --paper: #ffffff;
    --green: #1f5a37;
    --dark: #231f20;
  }
  * { margin: 0; padding: 0; box-sizing: border-box; }
  html, body { width: 928px; height: 1200px; overflow: hidden; background: var(--paper); }
  .page {
    position: relative; width: 928px; height: 1200px; overflow: hidden;
    font-family: "Barlow", sans-serif; color: var(--ink); font-size: 19px; line-height: 25.5px;
  }
  .corner { position: absolute; }
  .corner-top { top: 0; left: 659px; }
  .corner-bottom { left: 0; top: 1099px; }
  .block { position: absolute; left: 80px; }
  .sub-title { font-weight: 700; font-size: 20px; }
  .section-title {
    font-family: "Righteous", sans-serif; color: var(--brand-red);
    font-size: 24px; line-height: 30px; text-transform: uppercase; letter-spacing: -0.3px;
  }
  .services { list-style: none; position: absolute; left: 140px; top: 348px; width: 690px; }
  .services li { position: relative; padding-left: 22px; margin-bottom: 14.5px; }
  .services li::before {
    content: ""; position: absolute; left: 0; top: 10px; width: 5px; height: 5px;
    border-radius: 50%; background: var(--brand-red);
  }
  .badges { position: absolute; top: 1115px; left: 291px; width: 600px; height: 56px; }
  .badge { position: absolute; display: flex; align-items: center; gap: 8px; font-weight: 700; }
  .badge-cadet { left: 0; top: 0; width: 179px; height: 54px; background: var(--dark); color: var(--paper); border-radius: 3px; justify-content: center; font-size: 17px; }
  .badge-green { left: 197px; top: 6px; height: 44px; color: var(--green); font-size: 22px; }
  .badge-green .dot { width: 22px; height: 22px; border-radius: 50%; background: var(--green); }
  .badge-safe { left: 384px; top: -3px; width: 62px; height: 62px; border-radius: 50%; background: var(--dark); }
  .badge-group { left: 467px; top: 7px; width: 94px; height: 40px; background: var(--brand-red); color: var(--paper); font-size: 13px; justify-content: center; border-radius: 2px; }
</style>
</head>
<body>
<div class="page">
  <svg class="corner corner-top" width="269" height="102" viewBox="0 0 269 102" role="img" aria-label="Red chevron band with Indigenous dot-art pattern">
    <polygon points="0,0 134,102 269,0 215,0 134,62 54,0" fill="var(--brand-red)"/>
  </svg>

  <section class="block" style="top:101px;">
    <h3 class="sub-title">Height Safety:</h3>
    <p>Design, test, and implementation of height safety systems.</p>
    <p>Inspection and replacement of Climbguard systems on towers.</p>
  </section>

  <section class="block" style="top:207px;">
    <h3 class="sub-title">Foundations:</h3>
    <p>Foundation solutions, from small slabs, piers, Geotech to turnkey construction jobs.</p>
    <p>Including grillage, floating slabs, Security Fencing, Gantry</p>
  </section>

  <h2 class="block section-title" style="top:305px;">Emergency Break Fix Services</h2>
  <ul class="services">
    <li>24/7 support with a rolling fleet of six trucks.</li>
    <li>Over 450 callouts per year.</li>
    <li>Purposely equipped and modified vehicles for the task.</li>
    <li>Over 4,000 emergency break fix calls answered in eight years.</li>
    <li>Supporting over 600 sites with fast, quality emergency break fix services.</li>
    <li>Experience with Trilumen on their expanding fibre and wireless network.</li>
    <li>Experience with Marvaske on the Velonet infrastructure on satellite and fixed wireless for the last 10 years during floods and bush fires.</li>
  </ul>

  <section class="block" style="top:662px;">
    <h2 class="section-title">Commitment to Safety</h2>
    <p>Prioritising the safety of our team and the communities we serve.</p>
    <p>Stringent safety protocols to ensure a secure working environment.</p>
    <p>“Pause Twice, Work Wise” culture.</p>
  </section>

  <section class="block" style="top:789px;">
    <h2 class="section-title">Commitment to Quality</h2>
    <p>Delivering top-notch workmanship.</p>
    <p>Skilled team using best practices and the latest technology.</p>
  </section>

  <section class="block" style="top:891px;">
    <h2 class="section-title">Commitment to Transparency</h2>
    <p>Honesty and openness in all business dealings.</p>
    <p>Keeping clients informed at every stage of the project.</p>
  </section>

  <svg class="corner corner-bottom" width="263" height="101" viewBox="0 0 263 101" role="img" aria-label="Red chevron band with Indigenous dot-art pattern">
    <polygon points="0,101 0,92 131,0 263,101 212,101 131,45 50,101" fill="var(--brand-red)"/>
  </svg>

  <div class="badges">
    <div class="badge badge-cadet">Quorvin Cadetship</div>
    <div class="badge badge-green"><span class="dot"></span>Quorvin Green</div>
    <div class="badge badge-safe" role="img" aria-label="Safety program badge"></div>
    <div class="badge badge-group">Quorvin Group</div>
  </div>
</div>
</body>
</html>
```